BOLD & MINIMALIST DESIGN NEEDED

We want a very bold but minimalistic business card design that is impactful and utilizes both sides of the business card. Our current logo is included for your use.

We want bold fonts and good use of negative space. We don't want the logo to overpower the design.

Target Market(s)

Professionals who are building new commercial buildings.

Industry/Entity Type

Construction

Contact Information for Business Card

Name, Title, email, office phone, cell phone, website

Font styles to use
Serif
Sans Serif

Requirements
Must have
• Bold design!

```html
<!DOCTYPE html>
<html lang="en">
<head>
<meta charset="utf-8">
<title>Summitline Business Card</title>
<link href="https://fonts.googleapis.com/css2?family=Roboto:wght@400;500;700;900&display=swap" rel="stylesheet">
<style>
  :root {
    --page-bg: #dcdcdc;
    --card-white: #f4f4f4;
    --ink: #111111;
    --ink-soft: #1d1d1d;
    --brand-green: #7dbb25;
    --green-light: #a9d46a;
    --green-deep: #78b820;
  }
  * { margin: 0; padding: 0; box-sizing: border-box; }
  html, body { width: 1200px; height: 1040px; overflow: hidden; }
  body {
    background: var(--page-bg);
    font-family: "Roboto", Arial, sans-serif;
    color: var(--ink);
    position: relative;
  }
  .card {
    position: absolute;
    left: 200px;
    width: 800px;
    height: 460px;
    border-radius: 22px;
    overflow: hidden;
    box-shadow: 0 3px 6px rgba(0,0,0,0.35);
  }
  .card-front { top: 50px; background: var(--card-white); }
  .card-back {
    top: 540px;
    background: radial-gradient(ellipse 60% 70% at 50% 50%, var(--green-light) 0%, #96c94d 50%, var(--green-deep) 100%);
  }

  /* front */
  .brand-lockup {
    position: absolute;
    left: 60px;
    top: 190px;
    width: 300px;
    display: flex;
    align-items: center;
    justify-content: center;
    gap: 12px;
  }
  .brand-mark {
    width: 26px; height: 26px;
    background: var(--brand-green);
  }
  .brand-name {
    font-weight: 900;
    font-size: 40px;
    letter-spacing: 0.5px;
    color: var(--ink);
  }
  .divider {
    position: absolute;
    left: 401px;
    top: 130px;
    width: 2px;
    height: 225px;
    background: #cfcfcf;
  }
  .contact {
    position: absolute;
    left: 425px;
    top: 132px;
  }
  .contact-name {
    font-weight: 700;
    font-size: 31px;
    line-height: 1;
    letter-spacing: 0.3px;
  }
  .contact-title {
    color: var(--brand-green);
    font-size: 20px;
    margin-top: 3px;
    margin-left: 2px;
  }
  .contact-address {
    font-size: 19.5px;
    line-height: 25px;
    margin-top: 14px;
    color: var(--ink-soft);
  }
  .contact-lines { list-style: none; margin-top: 14px; }
  .contact-lines li {
    display: flex;
    align-items: center;
    gap: 9px;
    font-size: 19.5px;
    line-height: 25px;
    color: var(--ink-soft);
  }
  .contact-lines svg { width: 18px; height: 18px; flex: none; }
  .front-stripe {
    position: absolute;
    left: 0; right: 0;
    top: 430px;
    height: 5px;
    background: var(--brand-green);
  }
  .front-band {
    position: absolute;
    left: 0; right: 0;
    top: 437px;
    bottom: 0;
    background: var(--ink);
  }

  /* back */
  .back-lockup {
    position: absolute;
    left: 0; right: 0;
    top: 160px;
    display: flex;
    align-items: center;
    justify-content: center;
    gap: 20px;
  }
  .back-mark { width: 44px; height: 44px; background: var(--ink); }
  .back-name {
    font-weight: 900;
    font-size: 72px;
    color: var(--ink);
    letter-spacing: 1px;
  }
  .back-url {
    position: absolute;
    left: 0; right: 0;
    top: 388px;
    text-align: center;
    font-size: 19px;
    color: var(--ink-soft);
  }
</style>
</head>
<body>

<section class="card card-front">
  <div class="brand-lockup">
    <span class="brand-mark"></span>
    <span class="brand-name">SUMMITLINE</span>
  </div>

  <div class="divider"></div>

  <div class="contact">
    <h1 class="contact-name">MARCUS HALE</h1>
    <p class="contact-title">President</p>
    <p class="contact-address">2190 Alder Crest Road<br>Glenmoor, NY 11930</p>
    <ul class="contact-lines">
      <li>
        <svg viewBox="0 0 24 24" aria-hidden="true"><path fill="#111" d="M6.6 10.8a15.1 15.1 0 0 0 6.6 6.6l2.2-2.2c.3-.3.7-.4 1-.2 1.1.4 2.3.6 3.6.6.6 0 1 .4 1 1V20c0 .6-.4 1-1 1A17 17 0 0 1 3 4c0-.6.4-1 1-1h3.5c.6 0 1 .4 1 1 0 1.3.2 2.5.6 3.6.1.3 0 .7-.2 1z"/></svg>
        (555) 0142-7780
      </li>
      <li>
        <svg viewBox="0 0 24 24" aria-hidden="true"><rect x="2" y="6" width="20" height="13" fill="#111"/><path d="M3 7l9 6 9-6" fill="none" stroke="#f4f4f4" stroke-width="1.6"/></svg>
        info@summitline.com
      </li>
      <li>
        <svg viewBox="0 0 24 24" aria-hidden="true"><circle cx="12" cy="12" r="10" fill="#111"/><path d="M2 12h20M12 2c3 3 3 17 0 20M12 2c-3 3-3 17 0 20" fill="none" stroke="#f4f4f4" stroke-width="1.3"/></svg>
        www.summitline.com
      </li>
    </ul>
  </div>

  <div class="front-stripe"></div>
  <div class="front-band"></div>
</section>

<section class="card card-back">
  <div class="back-lockup">
    <span class="back-mark"></span>
    <span class="back-name">SUMMITLINE</span>
  </div>
  <p class="back-url">www.summitline.com</p>
</section>

</body>
</html>
```